Highlight Document Over Image for Slide

We are seeking a graphic designer to overlay a news article on an image that pertains to the article, aiming for a stylish yet professional appearance. Given the limited resources, we encourage you to use your imagination and go beyond what basic tools like PowerPoint can offer.

```html
<!DOCTYPE html>
<html lang="en">
<head>
<meta charset="utf-8">
<title>Rule 20 – Introduction or Possession of Contraband Items</title>
<link href="https://fonts.googleapis.com/css2?family=Arimo:wght@400;700&display=swap" rel="stylesheet">
<style>
  :root {
    --bg-top: #fbfbfb;
    --bg-mid: #a9a9a9;
    --bg-bottom: #050505;
    --frame: #ffffff;
    --frame-line: #111111;
    --ink: #333333;
    --crescent: #1e1e1e;
    --panel: #ffffff;
    --hills: #b59a66;
    --hills-dark: #8f7a55;
    --campus: #7c7668;
    --roofs: #6f6a62;
    --water: #66655d;
    --water-deep: #5a5953;
  }
  * { margin: 0; padding: 0; box-sizing: border-box; }
  html, body { width: 1200px; height: 772px; overflow: hidden; }
  body {
    position: relative;
    font-family: "Arimo", Arial, sans-serif;
    color: var(--ink);
    background: linear-gradient(180deg, var(--bg-top) 0%, #e6e6e6 18%, var(--bg-mid) 42%, #4a4a4a 68%, var(--bg-bottom) 92%);
  }
  .slide-frame {
    position: absolute;
    left: 54px; top: 54px;
    width: 1091px; height: 668px;
    background: var(--frame);
    border: 2px solid var(--frame-line);
  }
  .site-photo {
    position: absolute;
    left: 90px; top: 90px;
    width: 1016px; height: 594px;
    background:
      radial-gradient(ellipse 30% 34% at 45% 52%, var(--roofs) 0%, rgba(111,106,98,0) 100%),
      radial-gradient(ellipse 45% 30% at 72% 18%, var(--hills-dark) 0%, rgba(143,122,85,0) 100%),
      radial-gradient(ellipse 40% 30% at 20% 95%, var(--water-deep) 0%, rgba(90,89,83,0) 100%),
      radial-gradient(ellipse 30% 40% at 95% 70%, var(--water) 0%, rgba(102,101,93,0) 100%),
      linear-gradient(180deg, var(--hills) 0%, #a98f62 14%, #92826a 30%, var(--campus) 50%, #746e62 66%, var(--water) 82%, var(--water-deep) 100%);
  }
  .shape-layer {
    position: absolute;
    left: 0; top: 0;
    width: 1200px; height: 772px;
  }
  .rule-panel {
    position: absolute;
    left: 741px; top: 404px;
    width: 431px;
  }
  .rule-head {
    display: flex;
    align-items: flex-start;
    margin-left: 106px;
  }
  .rule-number {
    font-weight: 700;
    font-size: 90px;
    line-height: 0.8;
    letter-spacing: -3px;
    margin-top: 7px;
    margin-right: 10px;
  }
  .rule-title {
    font-weight: 700;
    font-size: 20.5px;
    line-height: 25px;
    text-transform: uppercase;
  }
  .rule-body {
    margin-top: 12px;
    font-size: 16px;
    line-height: 19.6px;
  }
  .rule-body .line { display: block; text-align: justify; text-align-last: justify; white-space: nowrap; }
  .rule-body .line.end { text-align-last: left; }
  .page-number {
    position: absolute;
    left: 741px; top: 707px;
    font-size: 16px;
  }
</style>
</head>
<body>
  <div class="slide-frame"></div>
  <div class="site-photo" role="img" aria-label="Aerial photograph of a waterfront correctional facility campus: dry hills and houses at the top, walled buildings and yards in the centre, parking lots and the bay along the bottom"></div>

  <svg class="shape-layer" viewBox="0 0 1200 772" aria-hidden="true">
    <circle cx="996" cy="656" r="334" fill="var(--crescent)"/>
    <circle cx="1012" cy="650" r="328" fill="var(--panel)"/>
  </svg>

  <section class="rule-panel">
    <header class="rule-head">
      <div class="rule-number">20</div>
      <h1 class="rule-title">Introduction or<br>possession of<br>contraband items</h1>
    </header>
    <p class="rule-body">
      <span class="line">Employees shall not introduce or possess unauthorized</span>
      <span class="line">items such as escape paraphernalia, weapons, facsimiles of</span>
      <span class="line">weapons, ammunition, wireless communication devices, cell</span>
      <span class="line end">phones, tobacco or facsimiles of tobacco products</span>
      <span class="line">(e.g. electronic vapor cigarettes), lighters or any other item</span>
      <span class="line end">not specifically authorized by PD 04.04.100 "Custody,</span>
      <span class="line">Security and Safety Systems (Exempt)", OP 04.04.100</span>
      <span class="line">"Gate Security" or facility operating procedure in any facility</span>
      <span class="line">where offenders are housed. Employees are responsible for</span>
      <span class="line end">any item in their possession.</span>
    </p>
  </section>
  <div class="page-number">36</div>
</body>
</html>
```